BRTL web site redesign

Coastal Linkage Engineering service (BRTL) is a diverse technology company specialising in design and installation of fibre optics, network convergence and building services, for commercial clients in Australia, we required a new design of our website to attract new clients, generate sales leads, and provide information about our services to the market. The site and should have a new technology look and feel and be designed in word press. our branding colour is blue.

Target Market(s)

New developments, Construction organisations, Commercial end users, IT managers, Consultants.

Industry/Entity Type

It Company

Number of Pages Required

5+ page

Font styles to use
Sans Serif

Colors
0292cd
3176b5

Requirements
Must have
• key pages.
• Home page with some sizzle, automated pictures running through, I like the look of this competitor website http://www.gleamwirex.com.au/ good clean menus and easy to navigate.
• Services page our key services are Fibre optics, Security, Building services,Electrical. I would like the same page layout (Design) for all our services, with a find out more link on each page, manly picture driven with text around our key messaging.
• About us page with space for company profile and directors pictures, bio and contact information.
• Certifications / Accreditations page with have over 20 certifications on different products from suppliers, and a number of licences from governing bodies.
• Current and past projects page with case studies and customer outcomes
• Contact us page with options around what services they require more information on, please keep in mind the site is around generating sales Leeds and being seen as an industry expert.
Nice to have
• RSS feeds, Linked in link, to be placed within the design, Consistent BRTL branding,Same colour blue as our logo Document library for education information, white papers, presentations etc,
• a new technology look and feel, mobile friendly.
Should not have
• boring layout, move away from our cuurent website http://www.brtlgroup.com.au/
• no e eCommerce store required.

```html
<!DOCTYPE html>
<html lang="en">
<head>
<meta charset="utf-8">
<title>BRTL – Coastal Linkage Engineering Service</title>
<link href="https://fonts.googleapis.com/css2?family=Roboto:wght@400;500;700&display=swap" rel="stylesheet">
<style>
:root{
  --brand:#0292cd;
  --brand-deep:#3176b5;
  --cta:#2a63ae;
  --ink:#444;
  --heading:#2b6cb5;
  --dark:#1e1e1e;
  --nav:#2c2c2c;
  --light:#ececec;
  --white:#fff;
}
*{margin:0;padding:0;box-sizing:border-box}
html,body{width:1200px;height:2192px;overflow:hidden}
body{font-family:'Roboto',Arial,sans-serif;color:var(--ink);position:relative;background:var(--white)}
.abs{position:absolute}

/* header + hero */
.hero{left:0;top:0;width:1200px;height:636px;background:linear-gradient(135deg,#3a4a52 0%,#1d2a30 35%,#5a6a70 60%,#2a3338 100%)}
.topbar{left:0;top:0;width:1200px;height:60px;background:rgba(20,70,110,.85)}
.navbar{left:0;top:60px;width:1200px;height:64px;background:rgba(40,40,40,.9)}
.logo{left:89px;top:15px;width:216px;height:108px;background:var(--white);border:3px solid var(--brand-deep);display:flex;align-items:center;justify-content:center;gap:12px}
.logo .mark{width:30px;height:30px;background:var(--brand-deep)}
.logo .name{font-size:44px;font-weight:700;color:var(--brand-deep);letter-spacing:1px}
.top-phone{left:930px;top:23px;color:var(--white);font-size:14px;display:flex;align-items:center;gap:6px}
.signin{left:1049px;top:19px;width:62px;height:27px;border:1px solid #cfd8e0;border-radius:3px;color:var(--white);font-size:11px;display:flex;align-items:center;justify-content:center}
.nav a{position:absolute;top:85px;color:var(--white);font-size:13px;text-decoration:none}
.nav a.active{color:var(--brand)}
.dropdown{left:520px;top:124px;width:149px;height:107px;background:rgba(2,110,170,.85);padding:12px 0 0 18px}
.dropdown li{list-style:none;color:var(--white);font-size:13px;line-height:23px}
.dropdown li::before{content:"›";margin-right:8px}
.hero-photo{left:0;top:0;width:1200px;height:636px;background:linear-gradient(120deg,rgba(70,110,60,.45),rgba(20,30,40,.2) 40%,rgba(60,110,170,.35) 80%)}
.caption{left:117px;top:270px;width:475px;height:183px;background:rgba(10,60,110,.75);padding:32px 0 0 26px;color:var(--white)}
.caption h1{font-size:56px;font-weight:700;line-height:62px}
.caption p{font-size:37px;line-height:46px}
.arrow{top:325px}

/* welcome */
.welcome{left:0;top:636px;width:1200px;height:263px;text-align:center}
.welcome h2{position:absolute;top:40px;width:100%;font-size:23px;font-weight:500;color:var(--heading)}
.welcome p{position:absolute;left:105px;top:82px;width:991px;font-size:14px;line-height:26px}
.btn-blue{left:541px;top:184px;width:118px;height:36px;background:linear-gradient(#1e8ad6,#1567b8);border:1px solid #0d4f93;border-radius:3px;color:var(--white);font-size:13px;font-weight:500;display:flex;align-items:center;justify-content:center}

/* services */
.services{left:0;top:899px;width:1200px;height:370px;background:linear-gradient(90deg,#1770ab,#2a8bc5 50%,#1a6fa8)}
.services h2{position:absolute;top:26px;width:100%;text-align:center;color:var(--white);font-size:27px;font-weight:500}
.card{top:82px;width:249px}
.card .photo{width:249px;height:131px;border:2px solid #cfe4f2}
.card h3{margin-top:14px;color:var(--white);font-size:19px;font-weight:500}
.card p{margin-top:6px;color:#e0eef8;font-size:12px;line-height:18px;text-align:justify}
.btn-light{margin-top:12px;width:94px;height:34px;background:linear-gradient(#fff,#dcdcdc);border-radius:2px;color:#333;font-size:13px;display:flex;align-items:center;justify-content:center}

/* projects */
.projects{left:0;top:1269px;width:1200px;height:419px;background:linear-gradient(90deg,#171717,#3a3a3a 50%,#1a1a1a)}
.projects h2{position:absolute;top:44px;width:100%;text-align:center;color:var(--white);font-size:27px;font-weight:500}
.project-photo{left:89px;top:111px;width:402px;height:258px;background:linear-gradient(#5d88c6,#9bb6d8 45%,#4a5a44 75%,#3b3e3a)}
.project-text{left:491px;top:111px;width:624px;height:258px;background:#f4f4f4;padding:28px 24px}
.project-text h3{font-size:27px;font-weight:400;color:var(--heading);margin-bottom:10px}
.project-text p{font-size:12.5px;line-height:23px;color:#333;margin-bottom:23px}
.project-text a{color:var(--brand-deep);text-decoration:none}
.pager{top:128px;width:30px;height:21px;border:1px solid var(--brand-deep);background:var(--white)}

/* call to action */
.cta{left:0;top:1688px;width:1200px;height:132px;background:var(--cta)}
.cta-text{left:189px;top:34px;color:var(--white);font-size:41px;font-weight:400}
.btn-cta{left:800px;top:37px;width:276px;height:57px;background:linear-gradient(#1d86d2,#1569b8);border:1px solid #8fc2ea;border-radius:3px;color:var(--white);font-size:22px;font-weight:500;display:flex;align-items:center;justify-content:center}

/* footer */
.footer{left:0;top:1820px;width:1200px;height:219px;background:var(--light)}
.footer h4{position:absolute;top:38px;font-size:17px;font-weight:500;color:var(--heading)}
.footer .small{font-size:11px;line-height:19px;color:#444}
.news-item{left:422px;width:360px;display:flex;gap:14px}
.thumb{width:65px;height:54px;border:2px solid var(--white);box-shadow:0 0 2px #999;flex:none}
.news-item p{font-size:11px;line-height:17px;color:#444}
.news-item .date{color:var(--brand-deep)}
.mail{left:835px;top:139px;width:214px;height:33px;background:var(--white);border:1px solid #ccc;font-size:11px;color:#999;padding:10px}
.join{left:1049px;top:139px;width:59px;height:33px;background:var(--brand-deep);color:var(--white);font-size:12px;font-weight:500;display:flex;align-items:center;justify-content:center}

/* bottom bar */
.bottom{left:0;top:2039px;width:1200px;height:153px;background:#111;color:var(--white)}
.bottom .links{left:91px;top:51px;font-size:12px}
.bottom .copy{left:91px;top:73px;font-size:12px}
.bottom .social-label{left:756px;top:60px;font-size:11px}
.bottom .social-sub{left:756px;top:79px;font-size:10px}
.dot{top:51px;width:34px;height:34px;border-radius:50%;background:var(--brand-deep);border:2px solid #e0e0e0}
</style>
</head>
<body>

<!-- Header & hero -->
<div class="abs hero" role="img" aria-label="Photo of a technician's hands working a fibre optic fusion splicer with green cabling"></div>
<div class="abs hero-photo"></div>
<div class="abs topbar"></div>
<div class="abs navbar"></div>
<div class="abs logo"><span class="mark"></span><span class="name">BRTL</span></div>
<div class="abs top-phone">
  <svg width="13" height="13" viewBox="0 0 24 24"><path fill="#fff" d="M6.6 10.8a15 15 0 0 0 6.6 6.6l2.2-2.2c.3-.3.7-.4 1-.2 1.1.4 2.3.6 3.6.6.6 0 1 .4 1 1V20c0 .6-.4 1-1 1A17 17 0 0 1 3 4c0-.6.4-1 1-1h3.5c.6 0 1 .4 1 1 0 1.3.2 2.5.6 3.6.1.3 0 .7-.2 1z"/></svg>
  1300 555 019
</div>
<div class="abs signin">SIGN IN</div>
<nav class="nav">
  <a style="left:457px">HOME</a>
  <a class="active" style="left:519px">SERVICES ▾</a>
  <a style="left:615px">ABOUT US</a>
  <a style="left:706px">CERTIFICATIONS</a>
  <a style="left:840px">CURRENT / PAST PROJECTS</a>
  <a style="left:1038px">CONTACT US</a>
</nav>
<ul class="abs dropdown">
  <li>Fibre optics</li><li>Security</li><li>Building services</li><li>Electrical</li>
</ul>
<div class="abs caption"><h1>FIBRE OPTICS</h1><p>Installation and solutions</p></div>
<svg class="abs arrow" style="left:56px" width="34" height="66" viewBox="0 0 34 66"><polyline points="30,2 3,33 30,64" fill="none" stroke="#fff" stroke-width="2"/></svg>
<svg class="abs arrow" style="left:1110px" width="34" height="66" viewBox="0 0 34 66"><polyline points="4,2 31,33 4,64" fill="none" stroke="#fff" stroke-width="2"/></svg>

<!-- Welcome -->
<section class="abs welcome">
  <h2>WELCOME TO BRTL GROUP</h2>
  <p>Lorem Ipsum has been the industry's standard dummy text ever since the 1500s, when an unknown printer took a galley of type and scrambled it to make a type specimen book. It has survived not only five centuries, but also the leap into electronic typesetting, remaining essentially unchanged. It was popularised in the 1960s with the release of Letraset sheets containing Lorem Ipsum passages, and more recently with desktop publishing software</p>
  <div class="abs btn-blue">READ MORE</div>
</section>

<!-- Services -->
<section class="abs services">
  <h2>SERVICES</h2>
  <div class="abs card" style="left:90px">
    <div class="photo" role="img" aria-label="Glowing blue fibre optic strands" style="background:linear-gradient(135deg,#02101e,#0a4e7c 55%,#56b6e8)"></div>
    <h3>FIBRE OPTICS</h3>
    <p>Duis aute irure dolor in reprehenderit in voluptate velit esse cillum dolore eu fugiat</p>
    <div class="btn-light">Read More</div>
  </div>
  <div class="abs card" style="left:348px">
    <div class="photo" role="img" aria-label="Engineer with a laptop beside a server rack" style="background:linear-gradient(90deg,#7d8790,#c9cdd0 45%,#f2f2f2 60%,#3a3a3a)"></div>
    <h3>SECURITY</h3>
    <p>Duis aute irure dolor in reprehenderit in voluptate velit esse cillum dolore eu fugiat</p>
    <div class="btn-light">Read More</div>
  </div>
  <div class="abs card" style="left:606px">
    <div class="photo" role="img" aria-label="Construction workers in hard hats on a building site" style="background:linear-gradient(#c6ccd2,#9aa0a4 50%,#6b5436)"></div>
    <h3>BUILDING SERVICES</h3>
    <p>Duis aute irure dolor in reprehenderit in voluptate velit esse cillum dolore eu fugiat</p>
    <div class="btn-light">Read More</div>
  </div>
  <div class="abs card" style="left:864px">
    <div class="photo" role="img" aria-label="Row of orange electrical switchboards" style="background:linear-gradient(90deg,#b0441e,#e26a2c 50%,#c3552a)"></div>
    <h3>ELECTRICAL</h3>
    <p>Duis aute irure dolor in reprehenderit in voluptate velit esse cillum dolore eu fugiat</p>
    <div class="btn-light">Read More</div>
  </div>
</section>

<!-- Recent projects -->
<section class="abs projects">
  <h2>RECENT PROJECTS</h2>
  <div class="abs project-photo" role="img" aria-label="Tall residential tower covered in vertical gardens against a blue sky"></div>
  <div class="abs project-text">
    <h3>One Harbour Gardens</h3>
    <p>Harbour Gardens occupies nearly six hectares of the southern Sydney CBD, defining Sydney's 'downtown'. Harbour Gardens is the westmere visionary redevelopment of the old Kestrel Brewing site, bordered by Ridgeway and Tallow Streets in Marlowe.</p>
    <p>The site includes the protection of heritage buildings, new parklands and community facilities and substantial upgrades to urban infrastructure. <a>Read More &gt;&gt;</a></p>
  </div>
  <svg class="abs pager" style="left:1033px" viewBox="0 0 30 21"><polyline points="17,6 12,10.5 17,15" fill="none" stroke="#3176b5" stroke-width="1.6"/></svg>
  <svg class="abs pager" style="left:1069px" viewBox="0 0 30 21"><polyline points="13,6 18,10.5 13,15" fill="none" stroke="#3176b5" stroke-width="1.6"/></svg>
</section>

<!-- Call to action -->
<section class="abs cta">
  <svg class="abs" style="left:105px;top:37px" width="60" height="60" viewBox="0 0 60 60">
    <circle cx="30" cy="30" r="27" fill="none" stroke="#fff" stroke-width="3"/>
    <path fill="#fff" d="M22 17c1.5-1 3 0 3.8 1.6l1.8 3.7c.6 1.2.2 2.4-.8 3.2l-1.6 1.2c1.2 3 3.4 5.3 6.4 6.6l1.3-1.6c.8-1 2.1-1.3 3.2-.7l3.6 1.9c1.6.9 2.4 2.5 1.3 3.9-1.8 2.4-4.6 3.7-7.3 2.9C26 41 19.5 34.4 17.9 26.7c-.6-3.5 1.4-7.6 4.1-9.7z"/>
  </svg>
  <div class="abs cta-text">Call Us Today ! 1300 555 019</div>
  <div class="abs btn-cta">CONTACT US</div>
</section>

<!-- Footer -->
<footer class="abs footer">
  <h4 style="left:89px">CONTACT INFO</h4>
  <div class="abs small" style="left:91px;top:72px">Suite 4B, 12-14 Merrow Lane<br>Kellyvale NSW 2160<br>PO Box 2290 NSW 1770</div>
  <div class="abs small" style="left:91px;top:140px;line-height:22px">
    <svg width="10" height="10" viewBox="0 0 24 24"><path fill="#2b6cb5" d="M6.6 10.8a15 15 0 0 0 6.6 6.6l2.2-2.2c.3-.3.7-.4 1-.2 1.1.4 2.3.6 3.6.6.6 0 1 .4 1 1V20c0 .6-.4 1-1 1A17 17 0 0 1 3 4c0-.6.4-1 1-1h3.5c.6 0 1 .4 1 1 0 1.3.2 2.5.6 3.6.1.3 0 .7-.2 1z"/></svg>&nbsp; 1300 555 019<br>
    <svg width="10" height="8" viewBox="0 0 20 16"><rect width="20" height="16" rx="2" fill="#2b6cb5"/><polyline points="1,2 10,9 19,2" fill="none" stroke="#fff" stroke-width="2"/></svg>&nbsp; info@brtlmail.com
  </div>

  <h4 style="left:422px">LATEST NEWS</h4>
  <div class="abs news-item" style="top:70px">
    <div class="thumb" role="img" aria-label="Aerial view of a city park" style="background:linear-gradient(135deg,#4d7a46,#a8b6a0 60%,#d8dcd8)"></div>
    <p>Lorem ipsum dolor sit amet, consectetur adipisicing elit, sed do eiusmod tempor<br><span class="date">july 7, 2015</span></p>
  </div>
  <div class="abs news-item" style="top:137px">
    <div class="thumb" role="img" aria-label="Street view of city buildings" style="background:linear-gradient(135deg,#8fb4d8,#d8b890 60%,#b88a6a)"></div>
    <p>Lorem ipsum dolor sit amet, consectetur adipisicing elit, sed do eiusmod tempor<br><span class="date">july 7, 2015</span></p>
  </div>

  <h4 style="left:835px">NEWSLETTER</h4>
  <div class="abs small" style="left:835px;top:78px;font-size:12px;line-height:21px">Join our mailing list to stay up to date and get<br>notices about our new releases!</div>
  <div class="abs mail">mail@example.com</div>
  <div class="abs join">JOIN</div>
</footer>

<!-- Bottom bar -->
<div class="abs bottom">
  <div class="abs links">HOME &nbsp;|&nbsp; ABOUT &nbsp;|&nbsp; NEWS &nbsp;|&nbsp; BLOG &nbsp;|&nbsp; CONTACTS</div>
  <div class="abs copy">© 2015 &nbsp;Privacy Policy</div>
  <div class="abs social-label">SOCIAL NETWORKS</div>
  <div class="abs social-sub">Lorem Ipsum is simply dummy text</div>
  <div class="abs dot" style="left:951px" aria-label="Social network link"></div>
  <div class="abs dot" style="left:993px" aria-label="Social network link"></div>
  <div class="abs dot" style="left:1037px" aria-label="Social network link"></div>
  <div class="abs dot" style="left:1079px" aria-label="News feed link"></div>
</div>

</body>
</html>
```